High end Electrical/home automation Business Card

Need a card for a high end electrical and home automation company utilising the existing logo.
Phone
Email
Website

Like black look with raised detail. Don’t necessarily need to keep colour of logo it could be made grayscale or white etc

Target Market(s)

High end clients

Contact Information for Business Card

Brightmoor Electrical

Requirements
Must have
• Logo, phone, email, website, address

High end look
Nice to have
• Black background card
Raised font
Should not have
• Lots of colour

```html
<!DOCTYPE html>
<html lang="en">
<head>
<meta charset="utf-8">
<title>Brightmoor Electrical — Business Card</title>
<link href="https://fonts.googleapis.com/css2?family=Work+Sans:wght@400;500;700;800&display=swap" rel="stylesheet">
<style>
  :root {
    --page: #e9e9eb;
    --card-dark: #3a3a3c;
    --card-light: #ffffff;
    --ink: #3a3a3c;
    --ink-soft: #444446;
    --accent: #0a8bd6;
    --white: #ffffff;
  }
  * { margin: 0; padding: 0; box-sizing: border-box; }
  html, body {
    width: 1200px; height: 881px; overflow: hidden;
    background: var(--page);
    font-family: "Work Sans", Arial, sans-serif;
  }
  .sheet {
    width: 1200px; height: 881px;
    display: flex; flex-direction: column;
    align-items: center; justify-content: center; gap: 34px;
  }
  .card {
    width: 680px; height: 389px; position: relative; overflow: hidden;
    box-shadow: 0 10px 28px rgba(0,0,0,.18);
  }
  /* Front */
  .card--front {
    background: var(--card-dark);
    display: flex; align-items: center; justify-content: center;
  }
  .brand { display: flex; align-items: center; gap: 14px; }
  .brand__dot { width: 26px; height: 26px; border-radius: 50%; background: var(--accent); flex: none; }
  .brand__name { font-weight: 800; font-size: 38px; letter-spacing: -0.5px; white-space: nowrap; }
  .card--front .brand__name { color: var(--white); }

  /* Back */
  .card--back { background: var(--card-light); }
  .card--back .brand { position: absolute; left: 34px; top: 170px; gap: 10px; }
  .card--back .brand__dot { width: 20px; height: 20px; }
  .card--back .brand__name { color: var(--ink); font-size: 24px; }
  .divider {
    position: absolute; left: 350px; top: 100px;
    width: 2px; height: 176px; background: var(--accent);
  }
  .contact { position: absolute; left: 378px; top: 104px; color: var(--ink-soft); }
  .contact__name {
    color: var(--accent); font-weight: 500; font-size: 24px;
    letter-spacing: 2px; text-transform: uppercase; line-height: 1;
  }
  .contact__role { font-size: 15px; letter-spacing: 1px; margin-top: 6px; }
  .contact__address { font-size: 15px; letter-spacing: 1px; line-height: 1.35; margin-top: 16px; }
  .contact__list { list-style: none; margin-top: 14px; font-size: 15px; letter-spacing: 1px; line-height: 1.5; }
  .contact__list li { display: flex; align-items: center; gap: 8px; }
  .contact__list svg { width: 13px; height: 13px; flex: none; }
  .footer-bands { position: absolute; left: 0; bottom: 0; width: 680px; height: 48px; }
</style>
</head>
<body>
  <main class="sheet">
    <section class="card card--front" aria-label="Card front">
      <div class="brand">
        <span class="brand__dot"></span>
        <span class="brand__name">Brightmoor Electrical</span>
      </div>
    </section>

    <section class="card card--back" aria-label="Card back">
      <div class="brand">
        <span class="brand__dot"></span>
        <span class="brand__name">Brightmoor Electrical</span>
      </div>
      <div class="divider"></div>
      <div class="contact">
        <h1 class="contact__name">Daniel Hartwell</h1>
        <p class="contact__role">Founder</p>
        <p class="contact__address">418 Alder Row<br>Pinecrest, WA 99021</p>
        <ul class="contact__list">
          <li>
            <svg viewBox="0 0 16 16" aria-hidden="true"><path d="M4 1.5l2.5 3-1.5 1.7c.8 1.9 2.4 3.5 4.3 4.3L11 9l3 2.5-1.5 2.8C7 14 2 9 1.7 3.5z" fill="var(--accent)"/></svg>
            555 014 2287
          </li>
          <li>
            <svg viewBox="0 0 16 16" aria-hidden="true"><rect x="1.5" y="3.5" width="13" height="9" fill="none" stroke="var(--accent)" stroke-width="1.4"/><path d="M1.5 3.5L8 9l6.5-5.5" fill="none" stroke="var(--accent)" stroke-width="1.4"/></svg>
            hello@brightmoor.com
          </li>
          <li>
            <svg viewBox="0 0 16 16" aria-hidden="true"><g fill="none" stroke="var(--accent)" stroke-width="1.2"><circle cx="8" cy="8" r="6.5"/><ellipse cx="8" cy="8" rx="2.8" ry="6.5"/><path d="M1.5 8h13M2.5 4.8h11M2.5 11.2h11"/></g></svg>
            brightmoorelectrical.com
          </li>
        </ul>
      </div>
      <svg class="footer-bands" viewBox="0 0 680 48" preserveAspectRatio="none" aria-hidden="true">
        <polygon points="0,34 396,34 386,48 0,48" fill="var(--card-dark)"/>
        <polygon points="410,20 680,20 680,48 392,48" fill="var(--accent)"/>
      </svg>
    </section>
  </main>
</body>
</html>
```